Harbor Bath & Steam Digital Billboard

This is a digital billboard so we are looking for a fresh design that will capture people's attention. The current billboard is a simple black text "#GottaSteam" over a white background with a picture of an vexaphone with one of our photos (Reference attached) We enjoy how clean and simple this design is, but open to other concepts. Since the weather is getting colder, a lot of people come to our spa because we offer various dry saunas and hot baths in addition to our spa services. We have a few photos for reference on our website information view www.harborbathsteam.example , but you can email me for additional photo content - otto@harborbathsteam.example

Target Market(s)

New Jersey Locals

Colors
0255a3
ec1f27
f37122
ffc214

Requirements
Must have
• Font is "Barlow"
Nice to have
• #GottaSteam hashtag

```html
<!DOCTYPE html>
<html lang="en">
<head>
<meta charset="utf-8">
<title>Harbor Bath &amp; Steam — Digital Billboard</title>
<link rel="stylesheet" href="https://fonts.googleapis.com/css2?family=Barlow:wght@500;600;800&display=swap">
<style>
  :root {
    --brand-blue: #0255a3;
    --steam-teal: #6fcfd6;
    --sun-yellow: #ffc214;
    --paper: #ffffff;
    --ink: #111111;
    --stage: #101010;
    --wood-light: #e2c4a4;
    --wood-mid: #cda783;
  }
  * { box-sizing: border-box; margin: 0; padding: 0; }
  html, body {
    width: 1200px; height: 1200px; overflow: hidden;
    background: var(--stage);
    font-family: "Barlow", sans-serif;
  }
  .billboard {
    position: absolute;
    left: 20px; top: 431px;
    width: 1160px; height: 338px;
    background: var(--brand-blue);
    overflow: hidden;
  }
  .billboard__photo {
    position: absolute;
    left: 0; top: 0;
    width: 500px; height: 267px;
    background: linear-gradient(90deg, var(--wood-light) 0%, var(--wood-mid) 50%, #5d85ad 82%, var(--brand-blue) 100%);
  }
  .brand {
    position: absolute;
    left: 640px; top: 62px;
    width: 420px;
    display: flex; align-items: center; justify-content: center; gap: 12px;
  }
  .brand__dot {
    width: 26px; height: 26px; border-radius: 50%;
    background: var(--paper);
  }
  .brand__name {
    color: var(--paper);
    font-weight: 600;
    font-size: 34px;
    letter-spacing: 1px;
  }
  .headline {
    position: absolute;
    right: 28px; top: 140px;
    font-weight: 800;
    font-size: 108px;
    line-height: 1;
    letter-spacing: -1px;
    white-space: nowrap;
  }
  .headline__lead { color: var(--steam-teal); }
  .headline__accent { color: var(--sun-yellow); }
  .contact-bar {
    position: absolute;
    left: 0; bottom: 0;
    width: 100%; height: 71px;
    background: var(--paper);
    display: flex; align-items: center; justify-content: space-between;
    padding: 0 46px 0 44px;
  }
  .contact {
    display: flex; align-items: center; gap: 14px;
    color: var(--ink);
    font-weight: 500;
    font-size: 29px;
  }
  .contact svg { flex: none; }
</style>
</head>
<body>
  <section class="billboard">
    <div class="billboard__photo" role="img" aria-label="Photo of a guest relaxing in a wooden sauna, wrapped in a towel"></div>

    <div class="brand">
      <span class="brand__dot"></span>
      <span class="brand__name">Harbor Bath &amp; Steam</span>
    </div>

    <h1 class="headline"><span class="headline__lead">#Gotta</span><span class="headline__accent">Steam</span></h1>

    <footer class="contact-bar">
      <div class="contact contact--email">
        <svg width="30" height="20" viewBox="0 0 30 20" aria-hidden="true">
          <rect x="1" y="1" width="28" height="18" fill="var(--brand-blue)"/>
          <path d="M1 1 L15 11 L29 1 M1 19 L11 9 M29 19 L19 9" stroke="#fff" stroke-width="2" fill="none"/>
        </svg>
        <span>otto@harborbathsteam.example</span>
      </div>
      <div class="contact contact--web">
        <svg width="28" height="28" viewBox="0 0 28 28" aria-hidden="true" fill="none" stroke="var(--brand-blue)" stroke-width="2.4">
          <circle cx="14" cy="14" r="12"/>
          <ellipse cx="14" cy="14" rx="5.5" ry="12"/>
          <path d="M2 14 H26 M4 8 H24 M4 20 H24"/>
        </svg>
        <span>www.harborbathsteam.example</span>
      </div>
    </footer>
  </section>
</body>
</html>
```